i need a business card design for my family investment company "quorin investments" based in dubai. its a diverse investment firm focusing on education, hospitality and automotive. the design has to be modern and try to incorporate the logo "E" in the design. details on card as follow

Yusuf K Bin Tarrah
Managing Director
yusuf@quorin-mail.ae
www.quorin-mail.ae

Harbor district,palwick tower, office 2212, dubai
tel. 04 3850927
mobile.050 9184203

card used for networking events and investor meetings

Hospitality

```html
<!DOCTYPE html>
<html lang="en">
<head>
<meta charset="utf-8">
<title>Quorin Investments – Business Card</title>
<link rel="stylesheet" href="https://fonts.googleapis.com/css2?family=Cinzel:wght@400;700&family=Jost:wght@300&display=swap">
<style>
  :root {
    --backdrop: #e4e4e4;
    --paper: #f7f7f6;
    --ink: #1f2328;
    --brand-blue: #4b6f91;
    --brand-blue-light: #5a7d9c;
    --brand-blue-dark: #2c4f72;
    --white: #ffffff;
  }
  * { margin: 0; padding: 0; box-sizing: border-box; }
  html, body {
    width: 1200px;
    height: 720px;
    overflow: hidden;
    background: var(--backdrop);
  }
  .canvas {
    position: relative;
    width: 1200px;
    height: 720px;
  }
  .card {
    position: absolute;
    top: 242px;
    width: 420px;
    height: 239px;
    overflow: hidden;
  }
  .card--front { left: 147px; background: var(--paper); }
  .card--back {
    left: 633px;
    background: linear-gradient(120deg, var(--brand-blue-light) 0%, var(--brand-blue) 45%, var(--brand-blue-dark) 100%);
  }

  .tab {
    position: absolute;
    width: 58px;
    height: 14px;
  }
  .card--front .tab { right: 0; background: var(--brand-blue); }
  .card--back .tab { left: 0; background: var(--paper); }
  .tab--top { top: 0; }
  .tab--middle { top: 101px; }
  .tab--bottom { bottom: 0; }

  .wordmark {
    position: absolute;
    font-family: "Jost", sans-serif;
    font-weight: 300;
    text-transform: uppercase;
    line-height: 1;
  }
  .wordmark__name, .wordmark__tagline { display: block; white-space: nowrap; }

  .card--front .wordmark { left: 24px; top: 20px; color: var(--ink); }
  .card--front .wordmark__name { font-size: 34px; letter-spacing: 0.42em; }
  .card--front .wordmark__tagline { font-size: 9px; letter-spacing: 1.28em; margin-top: 4px; }

  .card--back .wordmark { left: 103px; top: 90px; color: var(--white); }
  .card--back .wordmark__name { font-size: 50px; letter-spacing: 0.36em; }
  .card--back .wordmark__tagline { font-size: 12px; letter-spacing: 1.45em; margin-top: 10px; padding-left: 2px; }

  .holder {
    position: absolute;
    left: 24px;
    top: 86px;
    font-family: "Cinzel", serif;
    line-height: 1.05;
  }
  .holder__name { font-size: 12.5px; font-weight: 700; color: var(--brand-blue); }
  .holder__role { font-size: 9.5px; font-weight: 400; color: var(--ink); }

  .address {
    position: absolute;
    left: 24px;
    top: 126px;
    font-family: "Cinzel", serif;
    font-size: 9.5px;
    line-height: 12px;
    color: var(--ink);
    font-style: normal;
  }

  .contacts {
    position: absolute;
    left: 24px;
    top: 166px;
    list-style: none;
    font-family: "Cinzel", serif;
    font-size: 9.5px;
    color: var(--ink);
  }
  .contacts li {
    display: flex;
    align-items: center;
    height: 12px;
  }
  .contacts svg {
    width: 11px;
    height: 10px;
    margin-right: 9px;
    fill: var(--brand-blue-dark);
  }
</style>
</head>
<body>
<main class="canvas">

  <section class="card card--front" aria-label="Card front">
    <span class="tab tab--top"></span>
    <span class="tab tab--middle"></span>
    <span class="tab tab--bottom"></span>

    <div class="wordmark">
      <span class="wordmark__name">Quorin</span>
      <span class="wordmark__tagline">Investments</span>
    </div>

    <div class="holder">
      <p class="holder__name">Yusuf K Bin Tarrah</p>
      <p class="holder__role">Managing Director</p>
    </div>

    <address class="address">Harbor district, palwick tower,<br>office 2212, dubai</address>

    <ul class="contacts">
      <li>
        <svg viewBox="0 0 12 10" aria-hidden="true"><path d="M1 3.5C1 1.5 11 1.5 11 3.5L11 4.5 8.5 4.5 8.5 3.3 3.5 3.3 3.5 4.5 1 4.5Z"/><path d="M3 5 9 5 10.5 9.5 1.5 9.5Z"/></svg>
        04 3850927
      </li>
      <li>
        <svg viewBox="0 0 12 10" aria-hidden="true"><path d="M3.5 0H8.5V10H3.5Z M4.5 1.2V7.8H7.5V1.2Z" fill-rule="evenodd"/></svg>
        050 9184203
      </li>
      <li>
        <svg viewBox="0 0 12 10" aria-hidden="true"><path d="M0.5 1.5H11.5V8.5H0.5Z M1.5 2.4 6 5.8 10.5 2.4V7.6H1.5Z" fill-rule="evenodd"/></svg>
        yusuf@quorin-mail.ae
      </li>
      <li>
        <svg viewBox="0 0 12 10" aria-hidden="true"><path d="M1 1H11V7.5H1Z M2 2V6.5H10V2Z M4 8.5H8V9.5H4Z" fill-rule="evenodd"/></svg>
        www.quorin-mail.ae
      </li>
    </ul>
  </section>

  <section class="card card--back" aria-label="Card back">
    <span class="tab tab--top"></span>
    <span class="tab tab--middle"></span>
    <span class="tab tab--bottom"></span>

    <div class="wordmark">
      <span class="wordmark__name">Quorin</span>
      <span class="wordmark__tagline">Investments</span>
    </div>
  </section>

</main>
</body>
</html>
```